Local fast-growing company in the service sector

We are looking for a modern business card design, which should also appear on our letterheads

Target Market(s)

Private and industrial sectors

Contact Information for Business Card

Vorname Name
Kellberger Str. 18
73614 Lindenau
Tel.: 07146-839214-0
Name@agentur-kvtl.de

Colors
9d9d9d
919191
aaaaaa

Requirements
Must have
• The logo (file) in silver

```html
<!DOCTYPE html>
<html lang="de">
<head>
<meta charset="utf-8">
<title>KVTL Visitenkarte</title>
<link rel="stylesheet" href="https://fonts.googleapis.com/css2?family=Poppins:wght@400;500;600&display=swap">
<style>
  :root {
    --page-bg: #e6e6e6;
    --card-light: #d9d9d9;
    --card-dark: #7a7a7a;
    --card-darker: #5f5f5f;
    --silver: #aaaaaa;
    --logo-ink: #4a4a4a;
    --text-strong: #f4f4f4;
    --text-soft: #dcdcdc;
  }
  * { margin: 0; padding: 0; box-sizing: border-box; }
  html, body {
    width: 1200px;
    height: 969px;
    overflow: hidden;
    background: var(--page-bg);
    font-family: "Poppins", sans-serif;
  }
  .canvas {
    position: relative;
    width: 1200px;
    height: 969px;
  }
  .business-card {
    position: absolute;
    left: 100px;
    top: 200px;
    width: 1000px;
    height: 570px;
    border-radius: 26px;
    overflow: hidden;
    box-shadow: 0 18px 40px rgba(0,0,0,0.18);
  }
  .card-shapes {
    position: absolute;
    inset: 0;
    width: 100%;
    height: 100%;
  }
  .brand {
    position: absolute;
    left: 0;
    right: 0;
    top: 112px;
    text-align: center;
  }
  .brand-name {
    font-size: 96px;
    font-weight: 600;
    letter-spacing: 4px;
    color: var(--logo-ink);
    line-height: 1;
  }
  .holder {
    position: absolute;
    left: 50px;
    top: 426px;
  }
  .holder-name {
    font-size: 29px;
    font-weight: 500;
    color: var(--text-strong);
    line-height: 1.2;
    margin-bottom: 6px;
  }
  .holder-address {
    font-size: 22px;
    font-weight: 400;
    color: var(--text-soft);
    line-height: 1.45;
  }
  .contact-list {
    position: absolute;
    right: 42px;
    top: 432px;
    list-style: none;
  }
  .contact-item {
    display: flex;
    align-items: center;
    justify-content: flex-end;
    gap: 14px;
    font-size: 22px;
    color: var(--text-soft);
    line-height: 1.45;
  }
  .contact-icon {
    width: 22px;
    height: 22px;
    fill: var(--text-strong);
    flex: none;
  }
</style>
</head>
<body>
<main class="canvas">
  <section class="business-card" aria-label="Visitenkarte KVTL">
    <svg class="card-shapes" viewBox="0 0 1000 570" preserveAspectRatio="none" aria-hidden="true">
      <defs>
        <linearGradient id="darkPanel" x1="0" y1="0" x2="0" y2="1">
          <stop offset="0" stop-color="#7a7a7a"/>
          <stop offset="1" stop-color="#5f5f5f"/>
        </linearGradient>
        <linearGradient id="lightPanel" x1="0" y1="0" x2="0" y2="1">
          <stop offset="0" stop-color="#e4e4e4"/>
          <stop offset="1" stop-color="#d9d9d9"/>
        </linearGradient>
      </defs>
      <rect class="dark-panel" width="1000" height="570" fill="url(#darkPanel)"/>
      <path class="fold-edge" d="M0,62 L360,432 Q500,536 640,432 L1000,62 L1000,48 L640,416 Q500,516 360,416 L0,48 Z" fill="#aaaaaa"/>
      <path class="light-panel" d="M0,0 H1000 V48 L640,416 Q500,516 360,416 L0,48 Z" fill="url(#lightPanel)"/>
    </svg>

    <div class="brand">
      <div class="brand-name">KVTL</div>
    </div>

    <div class="holder">
      <p class="holder-name">Lukas Brenner</p>
      <p class="holder-address">Kellberger Str. 18</p>
      <p class="holder-address">73614 Lindenau</p>
    </div>

    <ul class="contact-list">
      <li class="contact-item">07146-839214-0
        <svg class="contact-icon" viewBox="0 0 24 24" aria-hidden="true"><path d="M6.6 10.8a15.1 15.1 0 0 0 6.6 6.6l2.2-2.2a1 1 0 0 1 1-.25 11.4 11.4 0 0 0 3.6.57 1 1 0 0 1 1 1V20a1 1 0 0 1-1 1A17 17 0 0 1 3 4a1 1 0 0 1 1-1h3.5a1 1 0 0 1 1 1c0 1.25.2 2.45.57 3.57a1 1 0 0 1-.25 1z"/></svg>
      </li>
      <li class="contact-item">Name@agentur-kvtl.de
        <svg class="contact-icon" viewBox="0 0 24 24" aria-hidden="true"><path d="M3 5h18a1 1 0 0 1 1 1v12a1 1 0 0 1-1 1H3a1 1 0 0 1-1-1V6a1 1 0 0 1 1-1zm0 2.2V17h18V7.2l-9 5.6z M4.2 7 12 11.8 19.8 7z"/></svg>
      </li>
      <li class="contact-item">www.agentur-kvtl.de
        <svg class="contact-icon" viewBox="0 0 24 24" aria-hidden="true"><path d="M12 2a10 10 0 1 0 0 20 10 10 0 0 0 0-20zm6.9 6h-3a15.6 15.6 0 0 0-1.4-3.6A8 8 0 0 1 18.9 8zM12 4c.8 1.2 1.5 2.5 1.9 4h-3.8c.4-1.5 1.1-2.8 1.9-4zM4.3 14a8 8 0 0 1 0-4h3.4a16.5 16.5 0 0 0 0 4zm.8 2h3a15.6 15.6 0 0 0 1.4 3.6A8 8 0 0 1 5.1 16zm3-8h-3a8 8 0 0 1 4.4-3.6A15.6 15.6 0 0 0 8.1 8zM12 20c-.8-1.2-1.5-2.5-1.9-4h3.8c-.4 1.5-1.1 2.8-1.9 4zm2.3-6H9.7a14.6 14.6 0 0 1 0-4h4.6a14.6 14.6 0 0 1 0 4zm.2 5.6a15.6 15.6 0 0 0 1.4-3.6h3a8 8 0 0 1-4.4 3.6zm1.8-5.6a16.5 16.5 0 0 0 0-4h3.4a8 8 0 0 1 0 4z"/></svg>
      </li>
    </ul>
  </section>
</main>
</body>
</html>
```